Advertising company unique advertising platform

we need a logo design for a new company based in Australia Melbourne. We develop innovated advertising platform where consumer can use this platform to get regular discount, as business owner they can use this platform for free advertisement. Payment for this advertisement platform only payable every two weeks, when I generate revenue for their business

Industry/Entity Type

Advertising

Contact Information for Business Card

Dale Morven | Co-Founder |Managing Director
Suite 718 240 Wattlebrook Lane Melbourne Vic 3000

ABN 38 614 207 923
Tel: +61 0487 259 318 | Email: dale.morven@plivorantu.com

Font styles to use
Decorative
Script

Requirements
Must have
• Try few different design and some round corner business card
Should not have
• One round corner business card...try 4 different colour background not only black, make sure two side is designed. Be creative so imagine you are giving this to a client make sure has wow factor, if you can also try one design with engrave like all the logo, words look 3d feel
• The word Advertising Platform use attached file font

```html
<!DOCTYPE html>
<html lang="en">
<head>
<meta charset="utf-8">
<title>Kestrelle Loop – Business Cards</title>
<link href="https://fonts.googleapis.com/css2?family=Roboto:wght@400;500;700&display=swap" rel="stylesheet">
<style>
  :root {
    --backdrop: #5b4a3e;
    --sun-yellow: #f6c93c;
    --flame-orange: #f08a2e;
    --ember-red: #e2452b;
    --card-black: #2a2a2a;
    --ink-dark: #1f1f1f;
    --name-red: #ef4a2e;
    --title-teal: #29e0b4;
    --text-light: #f2f2f2;
    --divider: #8a8a8a;
  }
  * { margin: 0; padding: 0; box-sizing: border-box; }
  html, body { width: 1200px; height: 886px; overflow: hidden; }
  body {
    background: var(--backdrop);
    font-family: "Roboto", Arial, sans-serif;
    position: relative;
  }
  .card {
    position: absolute;
    border-radius: 22px;
    overflow: hidden;
    box-shadow: 0 14px 30px rgba(0,0,0,.35);
  }

  /* Front */
  .card-front {
    left: 90px; top: 80px; width: 560px; height: 320px;
    background: radial-gradient(ellipse at 48% 38%, var(--sun-yellow) 0%, var(--flame-orange) 48%, var(--ember-red) 100%);
  }
  .front-brand {
    position: absolute; left: 0; right: 0; top: 118px;
    display: flex; align-items: center; justify-content: center; gap: 16px;
  }
  .brand-dot {
    width: 54px; height: 54px; border-radius: 50%;
    background: var(--ink-dark);
  }
  .front-brand .brand-name {
    font-size: 40px; font-weight: 700; color: var(--ink-dark); letter-spacing: 1px;
  }
  .front-web {
    position: absolute; left: 0; right: 0; top: 246px;
    text-align: center; font-size: 15px; letter-spacing: 6px; color: var(--ink-dark);
  }

  /* Back */
  .card-back {
    left: 560px; top: 440px; width: 580px; height: 330px;
    background: var(--card-black);
  }
  .back-brand {
    position: absolute; left: 28px; top: 90px; width: 250px;
    display: flex; align-items: center; gap: 12px;
  }
  .back-brand .brand-dot {
    width: 48px; height: 48px; flex: none;
    background: var(--flame-orange);
  }
  .back-brand .brand-name {
    font-size: 29px; font-weight: 700; color: var(--flame-orange); line-height: 1.1;
  }
  .divider {
    position: absolute; left: 296px; top: 50px; width: 2px; height: 150px;
    background: var(--divider);
  }
  .contact {
    position: absolute; left: 318px; top: 62px; right: 16px;
  }
  .contact-name {
    font-size: 23px; font-weight: 500; color: var(--name-red); text-transform: uppercase;
  }
  .contact-title {
    font-size: 17px; font-weight: 500; color: var(--title-teal);
    text-transform: uppercase; line-height: 1.2; margin-top: 4px;
  }
  .contact-line {
    display: flex; align-items: center; gap: 9px;
    font-size: 15.5px; color: var(--text-light); margin-top: 8px;
  }
  .contact-line:first-of-type { margin-top: 12px; }
  .contact-line svg { width: 15px; height: 15px; flex: none; }
  .address-band {
    position: absolute; left: 0; right: 0; bottom: 0; height: 92px;
    background: linear-gradient(90deg, var(--ember-red) 0%, var(--flame-orange) 30%, var(--sun-yellow) 62%, var(--flame-orange) 85%, var(--ember-red) 100%);
  }
  .address {
    position: absolute; left: 50px; top: 20px; width: 420px;
    font-size: 16px; color: var(--ink-dark); text-align: center; line-height: 1.45;
    white-space: nowrap;
  }
  .band-dot {
    position: absolute; right: 40px; top: -22px;
    width: 48px; height: 48px; border-radius: 50%;
    background: var(--flame-orange); border: 3px solid var(--card-black);
  }
</style>
</head>
<body>

<section class="card card-front">
  <div class="front-brand">
    <div class="brand-dot"></div>
    <span class="brand-name">Kestrelle Loop</span>
  </div>
  <p class="front-web">www.plivorantu.com</p>
</section>

<section class="card card-back">
  <div class="back-brand">
    <div class="brand-dot"></div>
    <span class="brand-name">Kestrelle Loop</span>
  </div>
  <div class="divider"></div>
  <div class="contact">
    <p class="contact-name">Dale Morven</p>
    <p class="contact-title">Co-Founder<br>Managing Director</p>
    <p class="contact-line">
      <svg viewBox="0 0 24 24" aria-hidden="true"><path fill="#ef4a2e" d="M6.6 10.8a15.2 15.2 0 0 0 6.6 6.6l2.2-2.2a1 1 0 0 1 1-.25 11.4 11.4 0 0 0 3.6.57 1 1 0 0 1 1 1V20a1 1 0 0 1-1 1A17 17 0 0 1 3 4a1 1 0 0 1 1-1h3.5a1 1 0 0 1 1 1c0 1.250.2 2.450.57 3.57a1 1 0 0 1-.25 1z"/></svg>
      +61 0487 259 318
    </p>
    <p class="contact-line">
      <svg viewBox="0 0 24 24" aria-hidden="true"><rect x="2" y="5" width="20" height="14" rx="2" fill="#ef4a2e"/><path d="M3 6l9 7 9-7" fill="none" stroke="#2a2a2a" stroke-width="2"/></svg>
      dale.morven@plivorantu.com
    </p>
  </div>
  <div class="address-band">
    <p class="address">Plivorantu | ABN 38 614 207 923<br>Suite 718 240 Wattlebrook Lane, Melbourne Vic 3000</p>
    <div class="band-dot"></div>
  </div>
</section>

</body>
</html>
```